"Velmora Crest" sexual performance enhancement pill bottle label needed.

This should be interesting...

I am starting a line of sexual performance enhancement products. This will be the first of several products basically. Keep in mind, I am the type of business person to stay with one company for years if they provide me with quality work.

This particular product is a male sexual performance pill. The name of the product is "Velmora Crest." The packaging of the pills are a black bottle with a white top. Label on the product example would be perfect but at a minimum I have attached a "template" for your guidance.

Some of the technical aspects of this are as follows:

-File Format: Illustrator CS6 is preferred. (Winner must provide artwork in layer and can not flatten artwork.)
-Resolution: 300 dpi minimum
-Bleed: 1/16th (0.0625") inch from edge of label
-Color Mode: CMYK only or must be converted to CMYK for final production

Lastly, this is your project as a designer, artist, creator, this is essentially a piece of you that will be sold and known by thousands of people. I have no color scheme that I prefer, just use the template and follow the layout. If you have any further questions, please feel free to contact me at any time.
Updates

Quick note on the product and what it does: -Powerful, long lasting, harder erections -Works in a minutes and last for hours -Enhances sexual desire and drive Thank you for your ideas...

Project Deadline Extended
Reason: We decided to extent the project for a few more days to let the last few concepts come in. So far things are looking really good and we definitely have seen some amazing designs. Thank you for your hard work and amazing creativity. Looking forward to seeing what we have come in the next couple of day. Very respectfully, Brev

ONLY THREE DAYS LEFT!!!! Please submit your ideas as soon as possible. And as always, thank you for your help!!! V/r, Brev

Industry/Entity Type

Graphic Design

```html
<!DOCTYPE html>
<html lang="en">
<head>
<meta charset="utf-8">
<title>Velmora Crest – Bottle Label</title>
<link href="https://fonts.googleapis.com/css2?family=Oswald:wght@400;500;700&family=Roboto+Condensed:wght@400;700&display=swap" rel="stylesheet">
<style>
  :root {
    --backdrop: #c6c6c6;
    --label: #000000;
    --ink: #ffffff;
    --ink-soft: #e6e6e6;
    --accent-red: #e3202f;
    --headline-grey: #6f6f6f;
    --tagline-red: #e8313f;
    --seal-gold: #e0a21f;
    --seal-ring: #c1271f;
  }
  * { margin: 0; padding: 0; box-sizing: border-box; }
  html, body { width: 1200px; height: 681px; overflow: hidden; background: var(--backdrop); }
  .canvas { position: relative; width: 1200px; height: 681px; }

  .label {
    position: absolute; left: 80px; top: 113px; width: 1037px; height: 411px;
    background: var(--label); border-radius: 20px; color: var(--ink);
    font-family: "Roboto Condensed", "Arial Narrow", sans-serif;
  }
  .label > * { position: absolute; }

  /* Left panel: directions and warnings */
  .directions { left: 18px; top: 27px; width: 225px; font-size: 7.6px; line-height: 1.32; text-align: justify; }
  .directions p + p { margin-top: 4px; }
  .storage { left: 18px; top: 203px; width: 225px; font-size: 7.6px; line-height: 1.32; }
  .fda-note { left: 25px; top: 251px; width: 218px; font-size: 7.2px; line-height: 1.35; }
  .maker { left: 22px; top: 320px; font-size: 12px; line-height: 1.35; }

  /* Centre panel: brand */
  .brand { left: 288px; top: 25px; width: 474px; height: 157px; }
  .brand-square { position: absolute; left: 0; top: 0; width: 157px; height: 157px; background: var(--accent-red); }
  .brand-name {
    position: absolute; left: 178px; top: 8px;
    font-family: "Oswald", sans-serif; font-weight: 700; font-size: 54px; line-height: 62px;
    color: var(--ink); letter-spacing: 1px; text-transform: uppercase;
  }
  .seal { left: 424px; top: 138px; width: 56px; height: 56px; }

  .claims { left: 288px; top: 200px; width: 474px; font-family: "Oswald", sans-serif; }
  .claims-row { display: flex; height: 26.5px; align-items: center; }
  .claim-benefit { width: 181px; text-align: right; font-weight: 400; font-size: 22px; color: var(--ink); text-transform: uppercase; letter-spacing: -0.3px; }
  .claim-effect { margin-left: 6px; font-weight: 700; font-size: 22px; color: var(--headline-grey); text-transform: uppercase; letter-spacing: 1.6px; }
  .tagline { left: 288px; top: 286px; width: 382px; text-align: center; font-family: "Roboto Condensed", sans-serif; font-size: 15.5px; color: var(--tagline-red); text-transform: uppercase; }
  .count { left: 288px; top: 363px; width: 382px; text-align: center; font-family: "Oswald", sans-serif; color: var(--headline-grey); font-weight: 700; text-transform: uppercase; }
  .count-number { font-size: 20px; }
  .count-unit { font-size: 10px; }

  /* Right panel: supplement facts */
  .facts { left: 796px; top: 26px; width: 218px; }
  .facts-title { font-family: "Roboto Condensed", sans-serif; font-size: 27px; line-height: 1; letter-spacing: -0.3px; }
  .facts-serving { margin-top: 6px; font-size: 10px; line-height: 1.4; font-weight: 700; }
  .facts-rule { border-top: 1px solid var(--ink); }
  .facts-rule.thick { border-top-width: 2px; }
  .facts-head { display: flex; justify-content: space-between; font-size: 9.5px; padding: 6px 0 5px; margin-top: 8px; }
  .facts-row { display: flex; justify-content: space-between; font-size: 8.5px; font-weight: 700; margin-top: 8px; }
  .facts-blend { font-size: 8.5px; line-height: 1.5; text-align: justify; margin-top: 2px; padding-bottom: 32px; }
  .facts-note { font-size: 10px; margin-top: 10px; }
  .facts-other { font-size: 8.8px; line-height: 1.55; margin-top: 22px; }
</style>
</head>
<body>
<div class="canvas">
  <section class="label">

    <div class="directions">
      <p>SUGGESTED USE: As a dietary supplement, take two (2) capsules 1 hour before physical activity, or as directed by your health care professional. Do not exceed two (2) capsules daily.</p>
      <p>CAUTION: Do not exceed recommended dose. This product is not intended for pregnant or nursing mothers, children under the age of 18, or individuals taking prescription drugs. Discontinue use immediately if nausea, sleeplessness, or nervousness occur. Do not take this product if you have a known medical condition including high blood pressure, diabetes, any cardiovascular disorder, heart disease, hyperthyroidism, or are taking anti-depressant medications. If you have questions about the advisability of taking this product, consult your physician prior to use.</p>
    </div>

    <p class="storage">KEEP OUT OF THE REACH OF CHILDREN. DO NOT USE IF SAFETY SEAL IS DAMAGED OR MISSING. STORE AT ROOM TEMPERATURE.</p>

    <p class="fda-note">* These statements have not been evaluated by the Food and Drug Administration. This product is not intended to diagnose, treat, cure or prevent any disease.</p>

    <p class="maker">Manufactured Exclusively For:<br>COMPANY INFO</p>

    <div class="brand">
      <div class="brand-square"></div>
      <div class="brand-name">Velmora<br>Crest</div>
    </div>

    <svg class="seal" viewBox="0 0 56 56" role="img" aria-label="Quality seal">
      <circle cx="28" cy="28" r="27" fill="var(--seal-gold)"/>
    </svg>

    <div class="claims">
      <div class="claims-row"><span class="claim-benefit">Powerful</span><span class="claim-effect">Enhances</span></div>
      <div class="claims-row"><span class="claim-benefit">Long Lasting</span><span class="claim-effect">Sexual Desire</span></div>
      <div class="claims-row"><span class="claim-benefit">Harder Erections</span><span class="claim-effect">And Drive</span></div>
    </div>

    <p class="tagline">Works in a minutes and last for hours</p>

    <p class="count"><span class="count-number">60</span> <span class="count-unit">Tablets</span></p>

    <div class="facts">
      <h2 class="facts-title">Supplement Facts</h2>
      <p class="facts-serving">Serving Size: 2 Capsules<br>Servings Per Container: 30</p>
      <div class="facts-head facts-rule"><span>Amount Per Serving</span><span>% Daily Value</span></div>
      <div class="facts-rule"></div>
      <div class="facts-row"><span>VCX-Rx™ Proprietary Formula</span><span>1,560 mg &nbsp;†</span></div>
      <p class="facts-blend">Horny Goat Weed (herb powder), Maca (herb powder), Macuna Pruriens (L-Dopa), Polypodium Vulgare (herb powder), Yohimbe Bark (herb powder), Saw Palmetto (herb powder), Muira Puama (herb powder), Arginine (L-Arginine hydrochloride), Panax Ginseng (herb powder)</p>
      <div class="facts-rule thick"></div>
      <p class="facts-note">† % Daily Value not established</p>
      <p class="facts-other">Other Ingredients: Gelatin, Magnesium Stearate, and Calcium Carbonate.</p>
    </div>

  </section>
</div>
</body>
</html>
```